I need a SEO-friendly Wordpress website (making sure to style H1, H2, H3, etc correctly) for a Hawaii-based law firm called Meridian Crest Legal Group. Comparable websites include https://brvlaw.example/ and https://www.lomrit.example/ for design reference. The current copy on the TarnAdvocate.example website can be used.

```html
<!DOCTYPE html>
<html lang="en">
<head>
<meta charset="utf-8">
<title>Meridian Crest Legal Group – Kona Lawyers</title>
<link rel="stylesheet" href="https://fonts.googleapis.com/css2?family=Open+Sans:wght@300;400;600;700&family=Quicksand:wght@600;700&display=swap">
<style>
:root{
  --brand:#c0591b;
  --brand-soft:#e9c3a8;
  --ink:#222;
  --muted:#555;
  --band:#f4f0ed;
  --footer:#f4f4f4;
  --white:#fff;
}
*{box-sizing:border-box;margin:0;padding:0}
html,body{width:1200px;height:2489px;overflow:hidden}
body{font-family:"Open Sans",Arial,sans-serif;color:var(--ink);background:var(--white);position:relative}
.wrap{width:976px;margin:0 auto;position:relative}
a{color:inherit;text-decoration:none}

/* header */
.site-header{height:113px;position:relative}
.brand{position:absolute;left:0;top:30px}
.brand-name{font-family:"Quicksand",sans-serif;font-weight:700;font-size:25px;color:var(--brand);padding-bottom:4px;border-bottom:1px solid var(--brand);display:inline-block}
.brand-tag{font-size:10.5px;letter-spacing:2.6px;color:var(--brand);margin-top:6px}
.call{position:absolute;right:0;top:14px;font-size:16px;color:var(--brand);display:flex;align-items:center;gap:5px}
.call strong{font-size:20px;font-weight:600}
.main-nav{position:absolute;right:0;top:59px;display:flex;gap:30px;font-size:13px;color:#444}
.main-nav .current{color:var(--brand);font-weight:700}

/* hero */
.hero{height:603px;background:linear-gradient(120deg,#8a8a8a 0%,#cfcfcf 35%,#e6e6e6 55%,#7c7c7c 100%);position:relative}
.hero-card{position:absolute;left:365px;top:145px;width:469px;height:306px;border:2px solid var(--brand);background:rgba(255,255,255,.82);text-align:center;padding-top:54px}
.hero-card h1{font-size:32px;font-weight:600;color:var(--brand)}
.hero-card p{font-size:16px;color:var(--brand);line-height:23px;margin-top:10px}
.btn{display:inline-block;border:1px solid var(--brand);border-radius:4px;color:var(--brand);font-weight:600;font-size:16px;background:var(--white)}
.hero-card .btn{margin-top:28px;width:161px;height:46px;line-height:44px}
.dots{display:flex;gap:8px;justify-content:center;margin-top:40px}
.dots i{width:8px;height:8px;border-radius:50%;background:#fff;opacity:.9}
.dots i:first-child{background:none;border:1px solid #fff}

/* about */
.about{height:477px;position:relative}
.about-text{position:absolute;left:0;top:87px;width:540px}
.about h2{font-size:26px;font-weight:700;color:var(--brand)}
.about h3{font-size:20px;font-weight:300;color:var(--brand);margin-top:12px}
.about p{font-size:13.5px;line-height:21.5px;margin-top:16px}
.about p+p{margin-top:19px}
.about .btn{margin-top:38px;width:151px;height:45px;line-height:43px;text-align:center}
.about-photo{position:absolute;left:575px;top:88px;width:401px;height:299px;border:6px solid var(--brand-soft);border-radius:6px;background:linear-gradient(180deg,#2e2a48 0%,#4a3550 45%,#8a4a2a 80%,#3a2418 100%)}

/* practice */
.practice{height:468px;background:var(--band);text-align:center;padding-top:60px}
.section-title{font-size:26px;font-weight:700;color:var(--brand)}
.areas{display:flex;justify-content:space-between;margin-top:62px}
.area{width:230px}
.area-ring{width:124px;height:124px;border:2px solid var(--brand);border-radius:50%;margin:0 auto;display:flex;align-items:center;justify-content:center}
.area-ring span{width:58px;height:58px;border-radius:50%;background:#ead6c8}
.area h3{font-size:19px;font-weight:400;margin-top:12px;line-height:22px}
.area p{font-size:13px;color:#333;line-height:21px;margin-top:8px}

/* blog */
.blog{height:519px;text-align:center;padding-top:60px;position:relative}
.blog .intro{font-size:16px;color:#333;margin-top:14px}
.posts{display:flex;justify-content:space-between;margin-top:36px;text-align:left}
.post{width:308px}
.post-photo{height:156px}
.post h3{font-size:19px;font-weight:400;margin:24px 4px 0}
.post p{font-size:12.5px;line-height:21px;color:#333;margin:6px 4px 0}
.post time{display:block;font-size:10.5px;color:var(--brand);margin:16px 7px 0}
.arrow{position:absolute;top:190px}

/* footer */
.site-footer{height:312px;background:var(--footer);position:relative}
.footer-cols{position:relative;height:252px}
.footer-cols h4{font-size:13px;font-weight:700;color:var(--brand);letter-spacing:.3px}
.quick{position:absolute;left:0;top:55px}
.quick ul{list-style:none;display:grid;grid-template-columns:206px 100px;row-gap:12px;margin-top:25px;font-size:13px}
.contact{position:absolute;left:385px;top:55px;width:380px}
.contact ul{list-style:none;margin-top:24px;font-size:12.5px}
.contact li{display:flex;gap:6px;line-height:16px;margin-bottom:20px}
.contact svg{flex:none;margin-top:2px}
.social{position:absolute;right:0;top:55px}
.social ul{list-style:none;margin-top:25px;font-size:13px}
.social li{display:flex;align-items:center;gap:6px;margin-bottom:12px}
.social li i{width:10px;height:10px;background:var(--brand)}
.footer-bottom{border-top:1px solid #ddd;display:flex;justify-content:space-between;padding-top:22px;font-size:12.5px}
.legal{font-size:10px;color:#888}
</style>
</head>
<body>
<header class="site-header wrap">
  <div class="brand">
    <div class="brand-name">Meridian Crest Legal Group</div>
    <div class="brand-tag">DIVORCE AND PERSONAL INJURY LAWYERS</div>
  </div>
  <div class="call">
    <svg width="15" height="15" viewBox="0 0 24 24"><path fill="#c0591b" d="M6.6 10.8a15 15 0 0 0 6.6 6.6l2.2-2.2c.3-.3.7-.4 1-.2 1.1.4 2.3.6 3.6.6.6 0 1 .4 1 1V20c0 .6-.4 1-1 1A17 17 0 0 1 3 4c0-.6.4-1 1-1h3.5c.6 0 1 .4 1 1 0 1.3.2 2.5.6 3.6.1.3 0 .7-.2 1z"/></svg>
    Call Today: <strong>+1.808.555.0148</strong>
  </div>
  <nav class="main-nav">
    <a class="current" href="#">HOME</a><a href="#">ABOUT US</a><a href="#">ATTORNEYS</a><a href="#">PRACTICE AREAS</a><a href="#">BLOG</a><a href="#">CONTACT US</a>
  </nav>
</header>

<section class="hero" role="img" aria-label="Black and white photo of lawyers working at a laptop and signing documents">
  <div class="hero-card">
    <h1>Kona Lawyers of MCLG</h1>
    <p>Over 70 years of combined practice, specializing in<br>Personal Injury, Family &amp; Divorce,Child Custody</p>
    <a class="btn" href="#">LEARN MORE</a>
    <div class="dots"><i></i><i></i><i></i></div>
  </div>
</section>

<section class="about wrap">
  <div class="about-text">
    <h2>ABOUT THE KONA LAWYERS OF MCLG</h2>
    <h3>Lawyers Serving the Big Island and Neighboring Islands</h3>
    <p>The experienced attorneys in the Meridian Crest Legal Group's Kailua Kona, Hawaii office provide clients with a wide range of litigation expertise, including legal claims involving divorce &amp; family, personal injury, toxic exposures, intellectual property, and real estate.</p>
    <p>Our Kona office also offers commercial and hospitality litigation expertise on behalf of a wide variety of clients, including restaurants, hotels, property owners, and many others.</p>
    <a class="btn" href="#">LEARN MORE</a>
  </div>
  <div class="about-photo" role="img" aria-label="City skyline with lit skyscrapers at dusk"></div>
</section>

<section class="practice">
  <div class="wrap">
    <h2 class="section-title">OUR PRACTICE AREAS</h2>
    <div class="areas">
      <div class="area"><div class="area-ring"><span role="img" aria-label="Family icon"></span></div><h3>Family &amp; Divorce</h3><p>Sunt in culpa qui officia deserunt<br>mollit anim id est laborum sint<br>occaecat cupidatat.</p></div>
      <div class="area"><div class="area-ring"><span role="img" aria-label="Injured person icon"></span></div><h3>Personal Injury</h3><p>Sunt in culpa qui officia deserunt<br>mollit anim id est laborum sint<br>occaecat cupidatat.</p></div>
      <div class="area"><div class="area-ring"><span role="img" aria-label="Light bulb with key icon"></span></div><h3>Corporate &amp; Intellectual Property</h3><p>Sunt in culpa qui officia deserunt<br>mollit anim id est laborum sint<br>occaecat cupidatat.</p></div>
      <div class="area"><div class="area-ring"><span role="img" aria-label="Family in a house icon"></span></div><h3>Real Estate</h3><p>Sunt in culpa qui officia deserunt<br>mollit anim id est laborum sint<br>occaecat cupidatat.</p></div>
    </div>
  </div>
</section>

<section class="blog">
  <div class="wrap">
    <h2 class="section-title">LATEST BLOG</h2>
    <p class="intro">At vero eos et accusamus et iusto odio dignissimos ducimus</p>
    <div class="posts">
      <article class="post"><div class="post-photo" role="img" aria-label="Three professionals meeting in an office lounge" style="background:linear-gradient(90deg,#6b4a36,#d9d4cc 45%,#b8b2a6)"></div><h3>Numquam Eius Modi Tempora</h3><p>Class aptent taciti sociosqu ad litora torquent per co nubia nostra per inceptos hymenaeos</p><time>12 JAN 2018</time></article>
      <article class="post"><div class="post-photo" role="img" aria-label="Modern open-plan office interior" style="background:linear-gradient(90deg,#6f7d5c,#9a9890 45%,#3c3836)"></div><h3>Accusantium Doloremque Lauda</h3><p>Class aptent taciti sociosqu ad litora torquent per co nubia nostra per inceptos hymenaeos</p><time>25 FEB 2018</time></article>
      <article class="post"><div class="post-photo" role="img" aria-label="Hand placing a small wooden house model" style="background:linear-gradient(90deg,#2f3a4c,#c9b8a6 55%,#6b4b32)"></div><h3>Quia Consequuntur Magni Dolore</h3><p>Class aptent taciti sociosqu ad litora torquent per co nubia nostra per inceptos hymenaeos</p><time>12 MAR 2018</time></article>
    </div>
  </div>
  <svg class="arrow" style="left:57px" width="20" height="40" viewBox="0 0 20 40"><path d="M18 2 2 20l16 18" fill="none" stroke="#e3b592" stroke-width="1.5"/></svg>
  <svg class="arrow" style="left:1129px" width="20" height="40" viewBox="0 0 20 40"><path d="M2 2l16 18L2 38" fill="none" stroke="#e3b592" stroke-width="1.5"/></svg>
</section>

<footer class="site-footer">
  <div class="wrap">
    <div class="footer-cols">
      <div class="quick"><h4>QUICK LINKS</h4>
        <ul><li>Home</li><li>Blog</li><li>About Us</li><li>Gallery</li><li>Practice Areas</li><li>Site Map</li><li>Attorneys</li></ul>
      </div>
      <div class="contact"><h4>CONTACT US</h4>
        <ul>
          <li><svg width="12" height="13" viewBox="0 0 24 24"><path fill="#c0591b" d="M12 2a7 7 0 0 0-7 7c0 5 7 13 7 13s7-8 7-13a7 7 0 0 0-7-7zm0 9.5A2.5 2.5 0 1 1 12 6.5a2.5 2.5 0 0 1 0 5z"/></svg><span>Kona Lawyers of Meridian Crest Legal Group,42-1180 Palena Loop,<br>Suite 210,Kailua Kona, Hawaii 96745.</span></li>
          <li><svg width="12" height="12" viewBox="0 0 24 24"><path fill="#c0591b" d="M6.6 10.8a15 15 0 0 0 6.6 6.6l2.2-2.2c.3-.3.7-.4 1-.2 1.1.4 2.3.6 3.6.6.6 0 1 .4 1 1V20c0 .6-.4 1-1 1A17 17 0 0 1 3 4c0-.6.4-1 1-1h3.5c.6 0 1 .4 1 1 0 1.3.2 2.5.6 3.6.1.3 0 .7-.2 1z"/></svg><span>+1.808.555.0148</span></li>
          <li><svg width="13" height="11" viewBox="0 0 24 20"><path fill="#c0591b" d="M0 2h24v16H0zM2 4l10 7 10-7" stroke="#f4f4f4" stroke-width="1.5"/></svg><span>clients@tarnadvocate.example</span></li>
        </ul>
      </div>
      <div class="social"><h4>CONNECT WITH US</h4>
        <ul><li><i></i>Circlewall</li><li><i></i>Chirpline</li><li><i></i>Snapgrid</li><li><i></i>Streamreel</li></ul>
      </div>
    </div>
    <div class="footer-bottom">
      <span>Copyrights © 2019 Meridian Crest Legal Group. All rights reserved.</span>
      <span class="legal">Terms and Conditions | Privacy Policy</span>
    </div>
  </div>
</footer>
</body>
</html>
```